Young, dynamic furniture company needs a new business card design

We require a new business card design for our modern furniture company which supplies furniture and appliances to the property and development market.
Oakridge Interiors has become one of the leading furniture & appliance suppliers to the property market withing London. With over 10 years experience, we have increased our business to supply not only private landlords and managing agents, but also property developers, housing associations and local councils.
We offer not only a complete range of furniture which includes beds, wardrobes, dining sets and sofas, but also a high quality, full delivery and assembly service to help you with all our furnishing needs.

Target Market(s)

Private landlords, estate agents, letting agents, property management companies

Industry/Entity Type

Business

Contact Information for Business Card

Name,
Title,
Address,
Mobile,
Telephone,
Fax, Website, email address

Font styles to use
Sans Serif

Colors
3176b5
0555a3
85abd2
cfdeed

Requirements
Must have
• All the above information for each of our staff, along with our logo

```html
<!DOCTYPE html>
<html lang="en">
<head>
<meta charset="utf-8">
<title>Oakridge Interiors – Business Card</title>
<link rel="stylesheet" href="https://fonts.googleapis.com/css2?family=Montserrat:wght@400;500;600;700&family=Open+Sans:wght@400;600&display=swap">
<style>
  :root {
    --blue-deep: #0555a3;
    --blue-mid: #3176b5;
    --blue-light: #85abd2;
    --blue-pale: #cfdeed;
    --blue-navy: #173f8a;
    --cyan: #3fa2dc;
    --ink: #2b2b2e;
    --grey: #6b6d72;
    --paper: #f4f5f6;
    --stage: #e6e7ea;
  }
  * { margin: 0; padding: 0; box-sizing: border-box; }
  html, body { width: 1200px; height: 780px; overflow: hidden; }
  body {
    background: var(--stage);
    font-family: "Montserrat", "Open Sans", sans-serif;
    position: relative;
  }
  .card {
    position: absolute;
    border-radius: 16px;
    overflow: hidden;
    box-shadow: 0 10px 26px rgba(0, 0, 0, 0.18);
  }

  /* Front */
  .card-front {
    left: 115px; top: 110px;
    width: 350px; height: 560px;
    background: linear-gradient(160deg, #ffffff 0%, var(--paper) 100%);
  }
  .brand {
    position: absolute;
    left: 0; top: 70px;
    width: 240px;
    text-align: center;
  }
  .brand-mark {
    display: block;
    width: 34px; height: 34px;
    margin: 0 auto 16px;
    background: var(--blue-mid);
  }
  .brand-name {
    font-size: 18px;
    font-weight: 500;
    letter-spacing: 0.5px;
    color: var(--ink);
    text-transform: uppercase;
  }
  .brand-tagline {
    margin-top: 4px;
    font-size: 8.5px;
    font-weight: 500;
    letter-spacing: 0.6px;
    color: var(--grey);
    text-transform: uppercase;
  }
  .person {
    position: absolute;
    left: 26px; bottom: 60px;
  }
  .person-name {
    font-size: 19px;
    font-weight: 700;
    letter-spacing: 0.6px;
    text-transform: uppercase;
  }
  .person-name .first { color: var(--blue-navy); }
  .person-name .last { color: var(--cyan); }
  .person-title {
    margin-top: 2px;
    font-size: 15px;
    font-weight: 400;
    color: var(--ink);
  }
  .contact-band {
    position: absolute;
    right: 0; top: 0;
    width: 110px; height: 100%;
    background: linear-gradient(90deg, var(--blue-deep) 0%, #1e4fa0 100%);
  }
  .contact-lines {
    position: absolute;
    left: 30px; bottom: 24px;
    max-height: 510px;
    writing-mode: vertical-rl;
    transform: rotate(180deg);
    font-size: 11px;
    font-weight: 500;
    line-height: 22px;
    color: #ffffff;
    white-space: nowrap;
  }
  .contact-line { display: block; }
  .contact-lines .label { color: var(--cyan); }
  .contact-lines .sep { color: var(--cyan); padding: 3px 0; }

  /* Back */
  .card-back {
    left: 525px; top: 215px;
    width: 560px; height: 350px;
    background:
      linear-gradient(125deg, rgba(255,255,255,0.06) 0%, rgba(255,255,255,0) 45%),
      linear-gradient(160deg, #2356a8 0%, var(--blue-deep) 45%, #17458f 100%);
    color: #ffffff;
  }
  .back-content {
    position: absolute;
    left: 44px; top: 56px;
  }
  .back-name {
    font-size: 38px;
    font-weight: 500;
    letter-spacing: 1px;
    text-transform: uppercase;
    line-height: 1.05;
  }
  .back-tagline {
    margin-top: 8px;
    font-size: 21px;
    font-weight: 400;
    letter-spacing: 0.6px;
    text-transform: uppercase;
  }
  .back-office {
    margin-top: 28px;
    font-family: "Open Sans", sans-serif;
    font-size: 14px;
    font-weight: 400;
  }
  .back-address {
    margin-top: 10px;
    font-family: "Open Sans", sans-serif;
    font-size: 14px;
    font-weight: 400;
  }
</style>
</head>
<body>

  <section class="card card-front">
    <div class="brand">
      <span class="brand-mark"></span>
      <div class="brand-name">Oakridge Interiors</div>
      <div class="brand-tagline">Trade Furniture Solutions</div>
    </div>

    <div class="person">
      <div class="person-name"><span class="first">Marcus</span> <span class="last">Ellery</span></div>
      <div class="person-title">Managing Director</div>
    </div>

    <div class="contact-band">
      <div class="contact-lines">
        <div class="contact-line"><span class="label">T:</span> 020 7946 0312 <span class="sep">|</span> <span class="label">F:</span> 020 7946 0318 <span class="sep">|</span> <span class="label">M:</span> 07700 90 41 27</div>
        <div class="contact-line"><span class="label">E:</span> marcus@oakridge.co.uk <span class="sep">|</span> <span class="label">W:</span> www.oakridge.co.uk</div>
      </div>
    </div>
  </section>

  <section class="card card-back">
    <div class="back-content">
      <div class="back-name">Oakridge Interiors</div>
      <div class="back-tagline">Trade Furniture Solutions</div>
      <div class="back-office">Trade Showroom &amp; Office</div>
      <div class="back-address">22B Hollins Trade Park Walthamstow London, E17 5QT</div>
    </div>
  </section>

</body>
</html>
```